Landscaping flier 2024

Create a 1 page flier for landscaping services
1. Must be completed in Adobe Photoshop
2. Size 8.5" x 11" (portrait layout)
3. Include logo
4. Text to include:
2024 Gravesite Landscaping Packages
info@hollowbrookmemorial.org
(201) 555-0148
hollowbrookmemorial.org
5. Use chart text for the content. DO NOT COPY THE CHART DESIGN/FORMAT. Use the chart for the text you need only.
6. Use "Pricing cards as format for laying out the chart". Open to other ideas as well.
**Use the example of chart design (handwritten) to base your design off of.
7. Photos
-include before and after care photos

```html
<!DOCTYPE html>
<html lang="en">
<head>
<meta charset="utf-8">
<title>2024 Gravesite Landscaping Packages – Hollowbrook Memorial</title>
<link href="https://fonts.googleapis.com/css2?family=Poppins:wght@400;500;600;700;800&display=swap" rel="stylesheet">
<style>
:root{
  --maroon:#7c2b38;
  --maroon-deep:#6a2230;
  --charcoal:#333436;
  --row-a:#e4e4e4;
  --row-b:#f0f0f0;
  --row-sub:#dcdcdc;
  --pink-a:#d6c0c5;
  --pink-b:#efe9ea;
  --ink:#2b2b2b;
  --green:#2f7d1f;
  --red:#c62024;
  --badge:#d31f26;
  --page-bg:#ececec;
}
*{box-sizing:border-box;margin:0;padding:0}
html,body{width:783px;height:1200px;overflow:hidden;background:var(--page-bg);font-family:'Poppins',sans-serif;color:var(--ink)}
.flier{position:absolute;top:93px;left:0;width:783px;height:1013px;background:#fff;overflow:hidden;box-shadow:0 2px 10px rgba(0,0,0,.12)}

.brand{position:absolute;top:0;left:0;width:100%;height:113px;display:flex;align-items:center;justify-content:center;gap:14px}
.brand-mark{width:26px;height:26px;border-radius:50%;background:var(--maroon)}
.brand-name{font-weight:500;font-size:30px;letter-spacing:1px;color:var(--maroon);text-transform:uppercase}

.hero{position:absolute;top:113px;left:0;width:783px;height:298px}
.hero-sky{position:absolute;inset:0 0 175px 0;background:linear-gradient(100deg,#7a2a30 0%,#a04a32 35%,#8a3a2c 60%,#7c2b38 100%)}
.hero-notch{position:absolute;top:0;left:0}
.hero-title{position:absolute;top:18px;left:0;width:100%;text-align:center;color:#fff;line-height:1}
.hero-title .year{font-weight:400;font-size:46px}
.hero-title .main{font-weight:800;font-size:46px}
.hero-title .sub{display:block;font-weight:700;font-size:27px;margin-top:-4px}
.hero-photos{position:absolute;top:123px;left:0;width:783px;height:175px}
.label{position:absolute;bottom:6px;color:#fff;font-weight:700;font-size:14px;letter-spacing:.3px}
.label.before{left:49px}.label.after{right:55px}

.plans{position:absolute;top:432px;left:45px;width:689px;height:499px}
.card{position:absolute;top:0;display:flex;flex-direction:column}
.card.seasonal{left:0;width:231px}
.card.basic{left:238px;width:215px}
.card.perpetual{left:458px;width:231px}
.card-head{height:57px;border-radius:12px 12px 0 0;color:#fff;font-weight:600;font-size:14px;line-height:1.05;display:flex;flex-direction:column;justify-content:center;padding-left:0;position:relative;text-transform:uppercase}
.seasonal .card-head{background:var(--maroon);align-items:center}
.basic .card-head{background:var(--charcoal);align-items:center;text-align:center}
.perpetual .card-head{background:var(--maroon);padding-left:25px}
.card-head::after{content:"";position:absolute;bottom:-7px;left:50%;margin-left:-7px;border:7px solid transparent;border-bottom:0;border-top-color:inherit}
.seasonal .card-head::after,.perpetual .card-head::after{border-top-color:var(--maroon)}
.basic .card-head::after{border-top-color:var(--charcoal)}
.ribbon{position:absolute;top:-6px;right:18px;width:44px;height:54px}
.ribbon span{position:absolute;top:8px;left:0;width:100%;text-align:center;font-size:9.5px;font-weight:700;line-height:1;letter-spacing:-.2px;color:#fff}

.row{display:flex;align-items:center;padding-left:28px;gap:7px;font-size:11.5px;line-height:1.2}
.row svg{flex:none;width:14px;height:14px}
.sub-row{height:49px;justify-content:center;padding:0;text-align:center;font-weight:600;font-size:12.5px;line-height:1.2;background:var(--row-sub)}
.feature{height:77px;flex-direction:column;align-items:stretch;justify-content:center;padding:0 18px 0 28px}
.feature .feature-top{display:flex;align-items:center;gap:7px;font-weight:700;font-size:12px;line-height:1.2}
.feature small{display:block;font-size:7.2px;line-height:1.2;text-align:center;margin-top:2px;color:#444}
.r-mon{height:42px}.r-pay{height:49px}.r-box{height:61px}.r-rep{height:50px}.r-tru{height:50px}
.seasonal .feature,.basic .feature{background:var(--row-a)}
.seasonal .r-mon,.basic .r-mon,.seasonal .r-box,.basic .r-box,.seasonal .r-tru,.basic .r-tru{background:var(--row-b)}
.seasonal .r-pay,.basic .r-pay,.seasonal .r-rep,.basic .r-rep{background:var(--row-a)}
.perpetual .sub-row{background:var(--row-sub)}
.perpetual .feature,.perpetual .r-pay,.perpetual .r-rep{background:var(--pink-a)}
.perpetual .r-mon,.perpetual .r-box,.perpetual .r-tru{background:var(--pink-b)}
.card-body{border-radius:0 0 12px 12px;overflow:hidden;display:flex;flex-direction:column}

.price-band{position:absolute;top:435px;left:0;width:689px;height:64px;background:var(--maroon);border-radius:0 0 12px 12px;color:#fff;z-index:-1}
.plans{z-index:0}
.card{z-index:1}
.price{position:absolute;top:0;height:64px;display:flex;flex-direction:column;align-items:center;justify-content:center;text-align:center}
.price.seasonal-price{left:0;width:231px}
.price.basic-price{left:238px;width:215px;background:var(--maroon-deep)}
.price.perpetual-price{left:458px;width:231px}
.terms{display:flex;align-items:center}
.term{padding:0 10px;line-height:1}
.term+.term{border-left:1px solid #fff}
.term span{display:block;font-size:11px}
.term b{font-size:15px;font-weight:700}
.price small{font-size:6.5px;margin-top:4px}
.price .lead{font-size:6.5px}
.price .amount{font-size:22px;font-weight:700;line-height:1.05}

.contact{position:absolute;top:957px;left:45px;width:689px;display:flex;align-items:center;font-size:13.5px}
.valid{font-size:11px;line-height:1.1;width:103px}
.contact-item{display:flex;align-items:center;gap:5px;margin-right:9px}
.contact-item:last-child{margin-right:0}
.contact-item svg{width:17px;height:17px}
</style>
</head>
<body>
<svg width="0" height="0" style="position:absolute">
  <symbol id="tick" viewBox="0 0 14 14"><circle cx="7" cy="7" r="7" fill="#2f7d1f"/><path d="M3.8 7.2l2.2 2.2 4.2-4.4" fill="none" stroke="#fff" stroke-width="1.6" stroke-linecap="round" stroke-linejoin="round"/></symbol>
  <symbol id="cross" viewBox="0 0 14 14"><circle cx="7" cy="7" r="7" fill="#c62024"/><path d="M4.6 4.6l4.8 4.8M9.4 4.6l-4.8 4.8" stroke="#fff" stroke-width="1.7" stroke-linecap="round"/></symbol>
</svg>

<main class="flier">
  <header class="brand">
    <span class="brand-name">Hollowbrook</span>
    <span class="brand-mark" aria-hidden="true"></span>
    <span class="brand-name">Memorial</span>
  </header>

  <section class="hero">
    <div class="hero-sky" role="img" aria-label="Autumn trees in red and orange foliage"></div>
    <svg class="hero-notch" width="783" height="20" aria-hidden="true"><polygon points="305,0 482,0 464,18 323,18" fill="#fff"/></svg>
    <h1 class="hero-title"><span class="year">2024</span> <span class="main">Gravesite</span><span class="sub">Landscaping Packages</span></h1>
    <svg class="hero-photos" viewBox="0 0 783 175" role="img" aria-label="Before and after care photos of a gravesite with headstones, lawn and boxwood shrubs, joined by an autumn path">
      <defs>
        <linearGradient id="lawn" x1="0" y1="0" x2="0" y2="1"><stop offset="0" stop-color="#8a9a88"/><stop offset=".35" stop-color="#6f9a4a"/><stop offset="1" stop-color="#4f8a2c"/></linearGradient>
        <linearGradient id="autumn" x1="0" y1="0" x2="0" y2="1"><stop offset="0" stop-color="#8e3a2c"/><stop offset="1" stop-color="#c0622e"/></linearGradient>
      </defs>
      <rect width="783" height="175" fill="url(#lawn)"/>
      <polygon points="300,0 483,0 391,92" fill="url(#autumn)"/>
      <polygon points="391,92 320,175 462,175" fill="#6a3a2e"/>
      <rect x="0" y="148" width="783" height="27" fill="#264a1c" opacity=".75"/>
      <circle cx="391" cy="93" r="25" fill="#fff"/>
    </svg>
    <span class="label before">BEFORE CARE</span>
    <span class="label after">AFTER CARE</span>
  </section>

  <section class="plans">
    <article class="card seasonal">
      <h2 class="card-head">Seasonal Care</h2>
      <div class="card-body">
        <div class="row sub-row">Seasonal<br>landscaping care</div>
        <div class="row feature"><div class="feature-top"><svg><use href="#tick"/></svg><span>WEEDING &amp; TRIMMING<br>ON YOUR GRAVESITE</span></div><small>Approximately every 7 weeks during the<br>growing season : mid-April through<br>mid-October</small></div>
        <div class="row r-mon"><svg><use href="#cross"/></svg>Monument leveling</div>
        <div class="row r-pay"><svg><use href="#cross"/></svg>Payment Ensures grave<br>care forever</div>
        <div class="row r-box"><svg><use href="#cross"/></svg>Full bed of boxwood<br>shrubs</div>
        <div class="row r-rep"><svg><use href="#cross"/></svg>Replacement of<br>shrubs</div>
        <div class="row r-tru"><svg><use href="#cross"/></svg>Trust certificate</div>
      </div>
    </article>

    <article class="card basic">
      <h2 class="card-head">Basic Care<br>Endowment</h2>
      <div class="card-body">
        <div class="row sub-row">Landscaping care forever<br>with no plantings</div>
        <div class="row feature"><div class="feature-top"><svg><use href="#tick"/></svg><span>WEEDING &amp; TRIMMING<br>ON YOUR GRAVESITE</span></div><small>2 times per year : mid-May &amp;<br>mid-September</small></div>
        <div class="row r-mon"><svg><use href="#tick"/></svg>Monument leveling</div>
        <div class="row r-pay"><svg><use href="#tick"/></svg>Payment Ensures grave<br>care forever</div>
        <div class="row r-box"><svg><use href="#cross"/></svg>Full bed of boxwood<br>shrubs</div>
        <div class="row r-rep"><svg><use href="#cross"/></svg>Replacement of<br>shrubs</div>
        <div class="row r-tru"><svg><use href="#cross"/></svg>Trust certificate</div>
      </div>
    </article>

    <article class="card perpetual">
      <h2 class="card-head">Perpetual Care<br>Endowment</h2>
      <svg class="ribbon" viewBox="0 0 44 54" aria-hidden="true"><polygon points="0,0 44,0 44,44 22,54 0,44" fill="#d31f26"/></svg>
      <div class="ribbon" aria-hidden="false"><span>MOST<br>POPULAR</span></div>
      <div class="card-body">
        <div class="row sub-row">Landscaping care forever<br>for graves with plantings</div>
        <div class="row feature"><div class="feature-top"><svg><use href="#tick"/></svg><span>WEEDING &amp; TRIMMING<br>ON YOUR GRAVESITE</span></div><small>Approximately every 7 weeks during the<br>growing season : mid-April through<br>mid-October</small></div>
        <div class="row r-mon"><svg><use href="#tick"/></svg>Monument leveling</div>
        <div class="row r-pay"><svg><use href="#tick"/></svg>Payment Ensures grave<br>care forever</div>
        <div class="row r-box"><svg><use href="#tick"/></svg>Full bed of boxwood<br>shrubs</div>
        <div class="row r-rep"><svg><use href="#tick"/></svg>Replacement of<br>shrubs</div>
        <div class="row r-tru"><svg><use href="#tick"/></svg>Trust certificate</div>
      </div>
    </article>

    <div class="price-band">
      <div class="price seasonal-price">
        <div class="terms">
          <div class="term"><span>3 Years</span><b>$396</b></div>
          <div class="term"><span>2 Years</span><b>$264</b></div>
          <div class="term"><span>1 Years</span><b>$132</b></div>
        </div>
        <small>Multi-year payment locks in current rates</small>
      </div>
      <div class="price basic-price">
        <span class="lead">12 monthly payments of</span>
        <span class="amount">$287</span>
        <span class="lead">Call for single payment discount.</span>
      </div>
      <div class="price perpetual-price">
        <span class="lead">12 monthly payments of</span>
        <span class="amount">$351</span>
        <span class="lead">Call for single payment discount.</span>
      </div>
    </div>
  </section>

  <footer class="contact">
    <div class="valid">Valid through<br>10/31/2024</div>
    <div class="contact-item"><svg viewBox="0 0 18 18" aria-hidden="true"><circle cx="9" cy="9" r="8.2" fill="none" stroke="#2b2b2b" stroke-width="1.3"/><path d="M6.2 4.6l1.5 2.2-.9 1.1c.6 1.3 1.5 2.2 2.8 2.8l1.1-.9 2.2 1.5-.8 1.5c-3.4-.2-6.3-3.1-6.5-6.5z" fill="#2b2b2b"/></svg>(201) 555-0148</div>
    <div class="contact-item"><svg viewBox="0 0 18 18" aria-hidden="true"><circle cx="9" cy="9" r="8.2" fill="none" stroke="#2b2b2b" stroke-width="1.3"/><rect x="4.5" y="5.8" width="9" height="6.4" fill="none" stroke="#2b2b2b" stroke-width="1.2"/><path d="M4.5 5.8L9 9.4l4.5-3.6" fill="none" stroke="#2b2b2b" stroke-width="1.2"/></svg>info@hollowbrookmemorial.org</div>
    <div class="contact-item"><svg viewBox="0 0 18 18" aria-hidden="true"><circle cx="9" cy="9" r="8.2" fill="#2b2b2b"/><circle cx="9" cy="9" r="5" fill="none" stroke="#fff" stroke-width="1"/><path d="M4 9h10M9 4c-2.4 3-2.4 7 0 10M9 4c2.4 3 2.4 7 0 10" fill="none" stroke="#fff" stroke-width="1"/></svg>www.hollowbrookmemorial.org</div>
  </footer>
</main>
</body>
</html>
```